Finiding oppertunites in Real Estate 6.15.20

size of ad 7” x 9.6”
1-I like the ad to stand out and attract people's attention.
2-you should be able to see the text of the ad clearly .. see the attachment anything in yellow is instructions.
3-the list of topics should not be the main part of the ad
4-if you decide you want a picture or vector of a person .. (you decide)
then it should be a white male about 25-30 years old wearing a solid white or blue shirt and not long hair.
5-leave 1 inch for footer
see attachment
Good luck

Target Market(s)

potential male students 25-35 years of age

Industry/Entity Type

Education

Requirements
Must have
• will stand out and people would want to see it.
should be able to read the words of ad
Nice to have
• how to make money in real estate on one line

```html
<!DOCTYPE html>
<html lang="en">
<head>
<meta charset="utf-8">
<title>Real Estate Course Flyer</title>
<link rel="stylesheet" href="https://fonts.googleapis.com/css2?family=Jost:wght@400;600;800&family=Roboto+Condensed:wght@400;500;700&display=swap">
<style>
  :root {
    --backdrop: #5b5b5b;
    --paper: #f1f0ee;
    --gold: #8a6d3b;
    --gold-light: #d9c9a4;
    --gold-mid: #c4aa76;
    --frame-gold: #bda06a;
    --frame-fill: #b7985f;
    --navy: #1b1264;
    --red: #c8161d;
    --ink: #2f2f2f;
    --list-ink: #3a2f1e;
    --black: #111111;
  }
  * { margin: 0; padding: 0; box-sizing: border-box; }
  html, body { width: 1200px; height: 1200px; overflow: hidden; }
  body { background: var(--backdrop); position: relative; }

  .flyer {
    position: absolute; left: 183px; top: 10px;
    width: 834px; height: 1180px;
    background: var(--paper);
    overflow: hidden;
    font-family: "Roboto Condensed", "Arial Narrow", sans-serif;
  }
  .band-top {
    position: absolute; left: 0; top: 154px; width: 100%; height: 150px;
    background: linear-gradient(180deg, var(--gold-mid) 0%, #e4d9c1 35%, var(--paper) 100%);
  }
  .band-bottom {
    position: absolute; left: 0; top: 866px; width: 100%; height: 173px;
    background: linear-gradient(180deg, var(--paper) 0%, var(--gold-light) 40%, var(--gold-mid) 100%);
  }
  .course-title {
    position: absolute; top: 52px; width: 100%; text-align: center;
    font-family: "Jost", sans-serif; font-weight: 800; font-size: 66px;
    letter-spacing: 0.5px; color: var(--gold); line-height: 1;
  }
  .headline {
    position: absolute; top: 180px; width: 100%; text-align: center;
    font-weight: 700; font-size: 58px; color: var(--navy); line-height: 1;
    text-shadow: 2px 3px 4px rgba(0,0,0,0.25);
  }
  .tagline {
    position: absolute; top: 272px; width: 100%; text-align: center;
    font-weight: 500; font-size: 42px; line-height: 46px; color: var(--red);
  }
  .houses-photo {
    position: absolute; left: 0; top: 396px; width: 100%; height: 140px;
    background: radial-gradient(ellipse at 50% 70%, #ffffff 0%, #e2e2e2 55%, var(--paper) 100%);
  }
  .lesson-frame {
    position: absolute; left: 150px; top: 572px; width: 533px; height: 187px;
    border: 5px solid var(--frame-gold);
    background: var(--frame-fill);
  }
  .lesson-art {
    width: 100%; height: 100%;
    background: linear-gradient(90deg, var(--frame-fill) 0%, #a98c58 60%, #8f8f8f 80%, var(--frame-fill) 100%);
  }
  .sessions {
    position: absolute; top: 770px; width: 100%; text-align: center;
    font-weight: 500; font-size: 33px; color: var(--ink); line-height: 1.1;
  }
  .audience {
    position: absolute; top: 830px; width: 100%; text-align: center;
    font-weight: 500; font-size: 31px; color: var(--navy); line-height: 1.1;
  }
  .topics {
    position: absolute; top: 895px; left: 111px;
    display: grid; grid-template-columns: 246px 244px 220px;
  }
  .topic-column { list-style: none; }
  .topic {
    display: flex; align-items: center; gap: 12px;
    height: 25.7px; font-size: 14px; color: var(--list-ink);
  }
  .topic svg { width: 14px; height: 14px; flex: none; }
  .footer {
    position: absolute; left: 0; top: 1039px; width: 100%; height: 141px;
    background: var(--paper);
    font-size: 14px; color: var(--ink);
  }
  .address {
    position: absolute; left: 48px; top: 40px;
    display: flex; align-items: center; gap: 12px; line-height: 18px;
  }
  .address svg { width: 26px; height: 34px; }
  .contacts { position: absolute; left: 330px; top: 26px; list-style: none; }
  .contacts li {
    display: flex; align-items: center; gap: 12px; height: 23px;
  }
  .contacts svg { width: 16px; height: 16px; }
  .hotline {
    position: absolute; right: 46px; top: 30px; text-align: right;
    font-family: "Jost", sans-serif; line-height: 1;
  }
  .hotline-label { font-weight: 800; font-size: 33px; color: var(--red); }
  .hotline-number { font-weight: 800; font-size: 17px; color: var(--black); margin-top: 3px; }
</style>
</head>
<body>
  <main class="flyer">
    <div class="band-top"></div>
    <div class="band-bottom"></div>

    <h1 class="course-title">REAL ESTATE COURSE</h1>
    <h2 class="headline">How to Make Money in Real Estate?</h2>
    <p class="tagline">An investment in knowledge<br>opens up untold opportunities.</p>

    <div class="houses-photo" role="img" aria-label="Rows of small white model houses with one red house standing out in front"></div>

    <div class="lesson-frame">
      <div class="lesson-art" role="img" aria-label="Illustration of a young man in a blue shirt on a chair with a laptop, watching an online instructor on a large laptop screen with property and chart graphics"></div>
    </div>

    <p class="sessions">12 REMOTE SESSIONS - STARTING JUNE 16</p>
    <p class="audience">For those who have started or would like to go into Real Estate.</p>

    <div class="topics">
      <ul class="topic-column">
        <li class="topic"><svg viewBox="0 0 14 14"><rect x="1" y="2" width="10" height="10" fill="none" stroke="#b89a62" stroke-width="1.2"/><path d="M3.5 7 L6 9.5 L13 2" fill="none" stroke="#b89a62" stroke-width="1.4"/></svg>Single-family</li>
        <li class="topic"><svg viewBox="0 0 14 14"><rect x="1" y="2" width="10" height="10" fill="none" stroke="#b89a62" stroke-width="1.2"/><path d="M3.5 7 L6 9.5 L13 2" fill="none" stroke="#b89a62" stroke-width="1.4"/></svg>Multifamily</li>
        <li class="topic"><svg viewBox="0 0 14 14"><rect x="1" y="2" width="10" height="10" fill="none" stroke="#b89a62" stroke-width="1.2"/><path d="M3.5 7 L6 9.5 L13 2" fill="none" stroke="#b89a62" stroke-width="1.4"/></svg>Management</li>
        <li class="topic"><svg viewBox="0 0 14 14"><rect x="1" y="2" width="10" height="10" fill="none" stroke="#b89a62" stroke-width="1.2"/><path d="M3.5 7 L6 9.5 L13 2" fill="none" stroke="#b89a62" stroke-width="1.4"/></svg>Real Estate Concepts</li>
        <li class="topic"><svg viewBox="0 0 14 14"><rect x="1" y="2" width="10" height="10" fill="none" stroke="#b89a62" stroke-width="1.2"/><path d="M3.5 7 L6 9.5 L13 2" fill="none" stroke="#b89a62" stroke-width="1.4"/></svg>Real Estate law</li>
      </ul>
      <ul class="topic-column">
        <li class="topic"><svg viewBox="0 0 14 14"><rect x="1" y="2" width="10" height="10" fill="none" stroke="#b89a62" stroke-width="1.2"/><path d="M3.5 7 L6 9.5 L13 2" fill="none" stroke="#b89a62" stroke-width="1.4"/></svg>Investment properties</li>
        <li class="topic"><svg viewBox="0 0 14 14"><rect x="1" y="2" width="10" height="10" fill="none" stroke="#b89a62" stroke-width="1.2"/><path d="M3.5 7 L6 9.5 L13 2" fill="none" stroke="#b89a62" stroke-width="1.4"/></svg>Foreclosures</li>
        <li class="topic"><svg viewBox="0 0 14 14"><rect x="1" y="2" width="10" height="10" fill="none" stroke="#b89a62" stroke-width="1.2"/><path d="M3.5 7 L6 9.5 L13 2" fill="none" stroke="#b89a62" stroke-width="1.4"/></svg>Rehab</li>
        <li class="topic"><svg viewBox="0 0 14 14"><rect x="1" y="2" width="10" height="10" fill="none" stroke="#b89a62" stroke-width="1.2"/><path d="M3.5 7 L6 9.5 L13 2" fill="none" stroke="#b89a62" stroke-width="1.4"/></svg>Foreclosures</li>
        <li class="topic"><svg viewBox="0 0 14 14"><rect x="1" y="2" width="10" height="10" fill="none" stroke="#b89a62" stroke-width="1.2"/><path d="M3.5 7 L6 9.5 L13 2" fill="none" stroke="#b89a62" stroke-width="1.4"/></svg>Short sales</li>
      </ul>
      <ul class="topic-column">
        <li class="topic"><svg viewBox="0 0 14 14"><rect x="1" y="2" width="10" height="10" fill="none" stroke="#b89a62" stroke-width="1.2"/><path d="M3.5 7 L6 9.5 L13 2" fill="none" stroke="#b89a62" stroke-width="1.4"/></svg>Development</li>
        <li class="topic"><svg viewBox="0 0 14 14"><rect x="1" y="2" width="10" height="10" fill="none" stroke="#b89a62" stroke-width="1.2"/><path d="M3.5 7 L6 9.5 L13 2" fill="none" stroke="#b89a62" stroke-width="1.4"/></svg>Finical modeling</li>
        <li class="topic"><svg viewBox="0 0 14 14"><rect x="1" y="2" width="10" height="10" fill="none" stroke="#b89a62" stroke-width="1.2"/><path d="M3.5 7 L6 9.5 L13 2" fill="none" stroke="#b89a62" stroke-width="1.4"/></svg>HUD properties</li>
        <li class="topic"><svg viewBox="0 0 14 14"><rect x="1" y="2" width="10" height="10" fill="none" stroke="#b89a62" stroke-width="1.2"/><path d="M3.5 7 L6 9.5 L13 2" fill="none" stroke="#b89a62" stroke-width="1.4"/></svg>Due Diligence</li>
      </ul>
    </div>

    <footer class="footer">
      <div class="address">
        <svg viewBox="0 0 26 34"><path d="M13 1 C6 1 1 6 1 12.5 C1 20 13 28 13 28 C13 28 25 20 25 12.5 C25 6 20 1 13 1 Z" fill="#a8894f"/><path d="M8 13 L13 8.5 L18 13 V17.5 H8 Z" fill="#ffffff"/><ellipse cx="13" cy="32" rx="5" ry="1.6" fill="#a8894f"/></svg>
        <span>ur address goes here,<br>street Crossroad 123</span>
      </div>
      <ul class="contacts">
        <li><svg viewBox="0 0 16 16"><path d="M3 1.5 L6 1.5 L7 5 L5.2 6.3 C6 8.3 7.7 10 9.7 10.8 L11 9 L14.5 10 L14.5 13 C14.5 14 13.5 14.8 12.5 14.6 C7 13.8 2.2 9 1.4 3.5 C1.2 2.5 2 1.5 3 1.5 Z" fill="#a8894f"/></svg>+012 - 3456 - 78901</li>
        <li><svg viewBox="0 0 16 16"><rect x="1" y="3" width="14" height="10" fill="#a8894f"/><path d="M1 3 L8 9 L15 3" fill="none" stroke="#ffffff" stroke-width="1.2"/></svg>urname@email.com</li>
        <li><svg viewBox="0 0 16 16"><circle cx="8" cy="8" r="6.5" fill="none" stroke="#a8894f" stroke-width="1.6"/><path d="M8 1.5 V14.5 M1.5 8 H14.5" stroke="#a8894f" stroke-width="1.2"/></svg>urwebsitename.com</li>
      </ul>
      <div class="hotline">
        <div class="hotline-label">HOTLINE</div>
        <div class="hotline-number">+012 - 3456 - 78901</div>
      </div>
    </footer>
  </main>
</body>
</html>
```